Our website, is loosely based on a grant proposal submitted to the Northern Vessel Society last year for a community-based project that could improve the health of the community at large, I have attached this file for your review (underline "loosely). The idea is to create a "patient navigator" a website where patients can both learn and use as a resource for their care. I have been working on the project for some time, but my other responsibilities as a cardiologist have not allowed me time to learn and design a website of this type. Our website is intended for a spanish speaking audience and is in Spanish language. Designs in english will have to be translated. Our name: AcademiaBrisol.com: means a health university: One option is to have the website have a "university" theme. The project calls for: An initial: easy registration process: collecting name, DOB and city. Simplicity is key, many of our patients barely use computers, and this site is meant to make things easier, not complicate them. The web site should work as an extension of the doctors office, so it should be serious, creative, addictive, engaging. Doctors will see the patients in the office then refer them to the website to continue their learning about their conditions. There should be a page where patients can post questions: a panel of doctors: represented with their pictures, (in circles? around the question answered?) titles and small resumes (our "faculty") answers them. Every person that will attach themself to this website will have a title: doctors and nurses will be professors, residents and fellows will be assistant professors, aids can be PA?. The site should have a market place where people can purchase items that doctors recommend including foods, products and devices; here too, we can have a "bookshop". This should have a flexible mechanism for doctors to add their recommendations a patients can have access to them. Very important: there should be a site intended to be a classroom, this is the meat of this protect: where people can watch videos our staff will make to learn about different subjects; the site should keep track of the videos watched by the person and eventually "graduate them". These videos will be created by my staff, and added over time to the site, students should be able to "request" classes (videos). It should have a site where people can input their medications (notebook), have them stored and printed as a list if necessary. And finally it should have a contact and references section. We have set up a relationship with another site that help people count calories: and a link to this should be available. We have a link to our twitter account, This protect is intended to expand, and we hope to establish a long term relationship with the design team to expand it as needed in the future. The site is on PlanoWeb and can be seen in its current form at AcademiaBrisol.com . We have had a logo designed with specific colors of the hospital I work with and one plan is to present it to our hospital to adopt our page in it final form. Again, this site is in spanish and intended for a spanish audience.

Target Market(s)

Spanish speaking, late 30s to early 60s audience.

Industry/Entity Type

Community

Number of Pages Required

4 page

Font styles to use
Sans Serif

Colors
a64599
fceff5
3277b5

Requirements
Must have
• A simple, accesible look
Nice to have
• Animations, moving parts
Should not have
• English

```html
<!DOCTYPE html>
<html lang="es">
<head>
<meta charset="utf-8">
<title>AcademiaBrisol — Tu salud comienza hoy</title>
<link href="https://fonts.googleapis.com/css2?family=Roboto:wght@300;400;500;700&display=swap" rel="stylesheet">
<style>
:root{
  --magenta:#a64599;
  --blush:#fceff5;
  --blue:#3277b5;
  --blue-dark:#25568a;
  --navy:#1f3f66;
  --ink:#3a3a3a;
  --muted:#7a7a7a;
  --line:#e6d6e0;
  --white:#ffffff;
  --charcoal:#2e2f31;
}
*{box-sizing:border-box;margin:0;padding:0}
html,body{width:1200px;height:2206px;overflow:hidden}
body{position:relative;font-family:'Roboto',Arial,sans-serif;color:var(--ink);background:var(--white)}
.section{position:absolute;left:0;width:1200px}
.wordmark{font-family:'Roboto',Arial,sans-serif;font-weight:300;color:var(--magenta);letter-spacing:.5px}

/* header */
.site-header{top:0;height:82px;background:var(--white)}
.site-header .wordmark{position:absolute;left:171px;top:20px;font-size:30px}
.main-nav{position:absolute;left:477px;top:32px;display:flex;gap:30px;font-size:13px;color:#8a8a8a;text-transform:uppercase}
.main-nav .active{color:var(--magenta)}
.header-social{position:absolute;left:934px;top:33px;display:flex;gap:10px}
.header-social span{width:13px;height:13px;border-radius:50%;background:#b8b8b8;display:block}

/* hero */
.hero{top:82px;height:345px}
.hero-photo{position:absolute;inset:0;background:linear-gradient(100deg,#8d8f93 0%,#b9bbbe 35%,#6e7075 60%,#c9c3bf 85%,#a8a3a0 100%)}
.hero-emblem{position:absolute;left:528px;top:38px;width:140px;height:140px;border-radius:50%;background:var(--white)}
.hero-name{position:absolute;left:452px;top:203px;width:292px;height:47px;background:var(--white);display:flex;align-items:center;justify-content:center;font-size:30px}
.hero-tagline{position:absolute;left:422px;top:260px;width:353px;height:47px;background:var(--blush);color:var(--magenta);font-size:25px;display:flex;align-items:center;justify-content:center}

/* call bands */
.call-band{height:99px;background:var(--blue)}
.call-band p{position:absolute;left:171px;top:37px;color:var(--white);font-size:21px;text-transform:uppercase}
.call-band .btn-band{position:absolute;left:754px;top:25px;width:274px;height:49px;background:var(--blue-dark);color:var(--white);font-size:16px;font-weight:500;display:flex;align-items:center;justify-content:center}
.band-one{top:427px}
.band-two{top:1411px;height:97px}

/* welcome */
.welcome{top:526px;height:239px}
.welcome h1{position:absolute;left:171px;top:46px;font-weight:400;font-size:27px;color:var(--navy)}
.welcome h1 .wordmark{font-size:27px}
.welcome p{position:absolute;left:171px;top:87px;width:420px;font-size:11px;line-height:13px;color:#555}
.btn-magenta{position:absolute;background:var(--magenta);color:var(--white);font-size:13px;font-weight:500;display:flex;align-items:center;justify-content:center}
.welcome .btn-magenta{left:171px;top:150px;width:123px;height:36px}
.welcome-video{position:absolute;left:651px;top:29px;width:377px;height:182px;background:linear-gradient(90deg,#d9cfc4,#ece6df 50%,#c7c0b8);border:1px solid #ccc}
.play{position:absolute;left:162px;top:65px;width:52px;height:52px}

/* services */
.services{top:765px;height:331px}
.services-photo{position:absolute;inset:0;background:linear-gradient(90deg,#3b3c3f 0%,#5d5f63 22%,#3e3f42 45%,#2b2c2e 70%,#2f3032 100%)}
.services h2{position:absolute;left:627px;top:52px;font-size:38px;font-weight:400;color:var(--magenta)}
.services ul{position:absolute;left:631px;top:112px;list-style:none;color:var(--white);font-size:16px}
.services li{display:flex;align-items:center;gap:10px;height:30px}
.services p{position:absolute;left:631px;top:180px;width:397px;color:var(--white);font-size:11px;line-height:13px}
.services .btn-magenta{left:631px;top:236px;width:121px;height:34px}

/* three columns */
.columns{top:1096px;height:315px}
.quote-form{position:absolute;left:171px;top:32px;width:254px;height:249px;background:var(--blue);color:var(--white);text-align:center}
.quote-form h3{font-size:15px;font-weight:500;margin-top:16px}
.quote-form .lead{font-size:10px;font-weight:700;line-height:12px;margin:6px 20px 0}
.field{position:absolute;left:21px;width:209px;height:29px;background:var(--navy);font-size:10px;font-weight:700;text-align:left;padding:9px 14px;text-transform:uppercase}
.form-foot{position:absolute;left:21px;top:196px;width:209px;display:flex;justify-content:space-between;align-items:center;font-size:10px;font-weight:700}
.form-foot .send{width:97px;height:30px;background:var(--white);color:var(--blue);display:flex;align-items:center;justify-content:center;font-size:12px}
.classes h2{position:absolute;left:446px;top:50px;font-size:24px;font-weight:400;color:var(--blue)}
.classes p{position:absolute;left:446px;top:85px;width:270px;font-size:11px;line-height:13px;color:#555}
.classes-thumb{position:absolute;left:448px;top:190px;width:116px;height:68px;background:linear-gradient(90deg,#8b7a6c,#c7b7a8 60%,#e9e1d8)}
.classes .see{position:absolute;left:576px;top:215px;font-size:16px;color:#555}
.links-box{position:absolute;left:769px;top:43px;width:259px;height:228px;background:var(--blush)}
.links-box h3{font-size:19px;font-weight:400;color:var(--magenta);padding:18px 0 0 22px;height:58px}
.links-box ul{list-style:none}
.links-box li{height:42px;border-top:1px solid var(--line);display:flex;align-items:center;justify-content:space-between;padding:0 18px 0 22px;font-size:11px;color:var(--navy);text-transform:uppercase}

/* testimonials */
.voices{top:1508px;height:283px;background:var(--blush)}
.voice{position:absolute;width:400px;height:95px}
.voice .avatar{position:absolute;left:0;top:0;width:95px;height:95px;border-radius:50%;border:3px solid var(--magenta);background:linear-gradient(135deg,#c9a68c,#7d6a5e)}
.voice h4{position:absolute;left:110px;top:26px;font-size:11px;font-weight:700;color:var(--magenta)}
.voice p{position:absolute;left:110px;top:42px;width:290px;font-size:11px;line-height:13px;color:#555}

/* store tiles */
.store{top:1791px;height:233px}
.tile{position:absolute;top:34px;width:422px;height:169px;display:flex;align-items:center;justify-content:center;color:var(--blue);font-size:27px;font-weight:500;text-transform:uppercase}
.tile-library{left:171px;background:linear-gradient(90deg,#2a2520,#4a4038 50%,#2c2621)}
.tile-market{left:606px;background:linear-gradient(90deg,#3d3a44,#6a5c57 50%,#4a4d52)}

/* footer */
.site-footer{top:2024px;height:122px;background:var(--blush)}
.site-footer .wordmark{position:absolute;left:171px;top:40px;font-size:36px}
.footer-social{position:absolute;left:894px;top:48px;display:flex;gap:8px}
.footer-social span{width:28px;height:28px;border-radius:50%;background:#9a9a9a;display:block}
.legal{top:2146px;height:60px;text-align:center;font-size:12px;color:var(--muted);padding-top:20px}
</style>
</head>
<body>

<header class="section site-header">
  <div class="wordmark">AcademiaBrisol</div>
  <nav class="main-nav">
    <span class="active">Inicio</span><span>Acerca</span><span>Tienda</span><span>Blog</span><span>FAQ</span><span>Contacto</span>
  </nav>
  <div class="header-social"><span></span><span></span><span></span><span></span></div>
</header>

<section class="section hero">
  <div class="hero-photo" role="img" aria-label="Fotografía de médicos atendiendo a una paciente en consulta"></div>
  <div class="hero-emblem"></div>
  <div class="hero-name wordmark">AcademiaBrisol</div>
  <div class="hero-tagline">TU SALUD COMIENZA HOY!</div>
</section>

<section class="section call-band band-one">
  <p>Contacto EE.UU. ahora y obtenga la salud mejor!</p>
  <div class="btn-band">CITA AHORA</div>
</section>

<section class="section welcome">
  <h1>Bienvenidos al <span class="wordmark">AcademiaBrisol</span></h1>
  <p>Lorem ipsum dolor sit amet, consectetuer adipiscing elit, sed diam nonummy nibh euismod tincidunt ut laoreet dolore magna aliquam erat volutpat. Ut wisi enim ad minim veniam, quis nostrud exerci tation ullamcorper suscipit lobortis nisl ut aliquip ex ea commodo consequat. Autem vel eum iriure dolor in hendrerit in vulputate velit</p>
  <div class="btn-magenta">leer más</div>
  <div class="welcome-video" role="img" aria-label="Video: enfermera conversando con una paciente mayor">
    <svg class="play" viewBox="0 0 52 52"><circle cx="26" cy="26" r="24" fill="#3a3a3a" fill-opacity=".75" stroke="#fff" stroke-width="2"/><path d="M21 16 L37 26 L21 36 Z" fill="#fff"/></svg>
  </div>
</section>

<section class="section services">
  <div class="services-photo" role="img" aria-label="Fotografía de una doctora revisando una tableta"></div>
  <h2>NUESTROS SERVICIOS</h2>
  <ul>
    <li><svg width="16" height="14" viewBox="0 0 16 14"><path d="M1 1 L7 7 L1 13 M8 1 L14 7 L8 13" fill="none" stroke="#a64599" stroke-width="2"/></svg>PACIENTE APRENDER PARA EL CUIDADO</li>
    <li><svg width="16" height="14" viewBox="0 0 16 14"><path d="M1 1 L7 7 L1 13 M8 1 L14 7 L8 13" fill="none" stroke="#a64599" stroke-width="2"/></svg>USO RECURSOS DEL PACIENTE</li>
  </ul>
  <p>Lorem ipsum dolor sit amet, consectetuer adipiscing elit, sed diam nonummy nibh euismod tincidunt ut laoreet dolore magna aliquam erat volutpat. Ut wisi enim ad minim veniam, quis nostrud exerci tation ullamcorper suscipit...</p>
  <div class="btn-magenta">leer más</div>
</section>

<section class="section columns">
  <form class="quote-form">
    <h3>Obtenga ahora un Presupuesto!</h3>
    <p class="lead">Lorem ipsum dolor sit amet, consectetuer adipiscing</p>
    <div class="field" style="top:89px">Nombre</div>
    <div class="field" style="top:125px">Email</div>
    <div class="field" style="top:161px">Fecha de nacimiento</div>
    <div class="form-foot"><span>CONTACTO</span><span class="send">SEND</span></div>
  </form>

  <div class="classes">
    <h2>CLASES DE ESTUDIANTES</h2>
    <p>Lorem ipsum dolor sit amet, consectetuer adipiscing elit, sed diam nonummy nibh euismod tincidunt ut laoreet dolore magna aliquam erat volutpat. Ut wisi enim ad minim veniam, quis nostrud exerci tation ullamcorper suscipit lobortis nisl ut aliquip ex ea commodo consequat. Autem vel eum iriure dolor in hendrerit in vulputate velit</p>
    <div class="classes-thumb" role="img" aria-label="Miniatura de video de una clase"></div>
    <span class="see">Vea los videos!</span>
  </div>

  <aside class="links-box">
    <h3>ENLACES DE INTERÉS</h3>
    <ul>
      <li>Solicitud de clases<svg width="8" height="12" viewBox="0 0 8 12"><path d="M1 1 L6 6 L1 11" fill="none" stroke="#a64599" stroke-width="1.6"/></svg></li>
      <li>Navegación del paciente<svg width="8" height="12" viewBox="0 0 8 12"><path d="M1 1 L6 6 L1 11" fill="none" stroke="#a64599" stroke-width="1.6"/></svg></li>
      <li>Librería<svg width="8" height="12" viewBox="0 0 8 12"><path d="M1 1 L6 6 L1 11" fill="none" stroke="#a64599" stroke-width="1.6"/></svg></li>
      <li>FAQ<svg width="8" height="12" viewBox="0 0 8 12"><path d="M1 1 L6 6 L1 11" fill="none" stroke="#a64599" stroke-width="1.6"/></svg></li>
    </ul>
  </aside>
</section>

<section class="section call-band band-two">
  <p>Para aprender, para solicitar las clases de video!</p>
  <div class="btn-band">SOLICITUD DE CLASES</div>
</section>

<section class="section voices">
  <div class="voice" style="left:173px;top:34px">
    <div class="avatar" role="img" aria-label="Foto de una estudiante"></div>
    <h4>LOREM IPSUM DOLOR SIT AMET, ?</h4>
    <p>Lorem ipsum dolor sit amet, consectetuer adipiscing elit, diam nonummy nibh euismod tincidunt ut laoreet dolore.</p>
  </div>
  <div class="voice" style="left:630px;top:34px">
    <div class="avatar" role="img" aria-label="Foto de un estudiante con tableta"></div>
    <h4>LOREM IPSUM DOLOR SIT AMET, ?</h4>
    <p>Lorem ipsum dolor sit amet, consectetuer adipiscing elit, diam nonummy nibh euismod tincidunt ut laoreet dolore.</p>
  </div>
  <div class="voice" style="left:173px;top:154px">
    <div class="avatar" role="img" aria-label="Foto de una estudiante en computadora"></div>
    <h4>LOREM IPSUM DOLOR SIT AMET, ?</h4>
    <p>Lorem ipsum dolor sit amet, consectetuer adipiscing elit, diam nonummy nibh euismod tincidunt ut laoreet dolore.</p>
  </div>
  <div class="voice" style="left:630px;top:154px">
    <div class="avatar" role="img" aria-label="Foto de un estudiante sonriente"></div>
    <h4>LOREM IPSUM DOLOR SIT AMET, ?</h4>
    <p>Lorem ipsum dolor sit amet, consectetuer adipiscing elit, diam nonummy nibh euismod tincidunt ut laoreet dolore.</p>
  </div>
</section>

<section class="section store">
  <div class="tile tile-library" role="img" aria-label="Fotografía de una librería">Librería</div>
  <div class="tile tile-market" role="img" aria-label="Fotografía de pasillos de un mercado">Marketshop</div>
</section>

<footer class="section site-footer">
  <div class="wordmark">AcademiaBrisol</div>
  <div class="footer-social"><span></span><span></span><span></span><span></span></div>
</footer>

<div class="section legal">Derechos de autor © 2014 AcademiaBrisol</div>

</body>
</html>
```